The Neighbors Together Project

For submission to Lantern Campaign 2024
Need both Color and Black and White Versions
TITLE The Neighbors Together Project
Slogan; "Neighbors Together, one road...one Heart, just a different stride" -JT Pellow copyrights
Logo in Color and Logo in Black and White
Back of flyer will be The Field of Quiet Lanterns poem -JT Pellow
VOTE BLUE 2024 Header or Footer

I just want to thank you all for your participation in The Neighbors Together Project. In the next few days I will be reducing the choices down to 10. Id like for all of you to know Ive enjoyed seeing so many options and views on the Flyer. Mainly, I wanted to say to those who don't make the cut that I appreciate the work you've done.

LM Dorsey

```html
<!DOCTYPE html>
<html lang="en">
<head>
<meta charset="utf-8">
<title>The Neighbors Together Project – Flyer</title>
<link rel="stylesheet" href="https://fonts.googleapis.com/css2?family=Passion+One:wght@400;700&family=Oswald:wght@500;700&family=Poppins:wght@400;500;600&display=swap">
<style>
  :root {
    --backdrop: #7a7676;
    --paper: #ffffff;
    --ink-dark: #3b3b3b;
    --ink-mid: #6d6d6d;
    --ink-body: #222222;
    --tag-bg: #4a4a4a;
    --deco: #ececec;
  }
  * { margin: 0; padding: 0; box-sizing: border-box; }
  html, body { width: 1200px; height: 835px; overflow: hidden; }
  body { background: var(--backdrop); position: relative; font-family: "Poppins", sans-serif; }

  .flyer {
    position: absolute; top: 135px; width: 435px; height: 563px;
    background: var(--paper); overflow: hidden; text-align: center;
  }
  .flyer--front { left: 125px; }
  .flyer--back { left: 643px; }

  .corner-deco {
    position: absolute; top: 0; width: 130px; height: 150px;
    background: radial-gradient(ellipse at top, var(--deco) 0%, rgba(255,255,255,0) 70%);
  }
  .corner-deco--left { left: 0; }
  .corner-deco--right { right: 0; }

  /* Front */
  .brand-mark {
    position: absolute; top: 66px; left: 0; right: 0;
    display: flex; justify-content: center; align-items: center; gap: 8px;
    font-weight: 500; font-size: 13px; line-height: 18px;
    color: var(--ink-dark); letter-spacing: 0.5px;
  }
  .brand-mark__dot { width: 12px; height: 12px; border-radius: 50%; background: var(--ink-dark); }

  .front-title {
    position: absolute; top: 140px; left: 0; right: 0;
    font-family: "Passion One", sans-serif; font-weight: 700;
    font-size: 36px; line-height: 35px; color: var(--ink-dark); letter-spacing: 0.5px;
  }
  .flag-art { position: absolute; top: 195px; left: 0; width: 435px; height: 170px; }

  .slogan-lead {
    position: absolute; top: 346px; left: 0; right: 0;
    font-size: 19px; line-height: 24px; font-weight: 500; letter-spacing: 3.5px; color: var(--ink-body);
  }
  .slogan-big {
    position: absolute; top: 368px; left: 0; right: 0;
    font-family: "Oswald", sans-serif; font-weight: 700; font-size: 52px;
    line-height: 58px; color: var(--ink-mid); text-transform: uppercase;
  }
  .slogan-tail {
    position: absolute; top: 480px; left: 0; right: 0;
    font-family: "Oswald", sans-serif; font-weight: 700; font-size: 23px;
    line-height: 30px; color: var(--ink-dark); text-transform: uppercase;
  }
  .copyright-tag {
    position: absolute; top: 516px; left: 50%; transform: translateX(-50%);
    background: var(--tag-bg); color: #fff; font-size: 9px; line-height: 13px; font-weight: 600;
    letter-spacing: 1.5px; padding: 0 6px; white-space: nowrap;
  }

  /* Back */
  .poem-title {
    position: absolute; top: 36px; left: 0; right: 0;
    font-family: "Passion One", sans-serif; font-weight: 700;
    font-size: 44px; line-height: 42px; color: var(--ink-dark);
  }
  .poem-author {
    position: absolute; top: 123px; left: 0; right: 0;
    font-size: 13px; line-height: 18px; font-weight: 600; letter-spacing: 2.5px; color: var(--ink-body);
  }
  .poem-body {
    position: absolute; top: 172px; left: 50px; right: 50px;
    font-size: 10.2px; line-height: 13px; color: var(--ink-body);
  }
  .poem-body p { margin-bottom: 12.5px; }
  .poem-rule {
    position: absolute; top: 412px; left: 50%; width: 16px; height: 3px;
    margin-left: -8px; background: var(--ink-body);
  }
  .site-url {
    position: absolute; top: 436px; left: 0; right: 0;
    font-size: 12px; line-height: 16px; font-weight: 600; letter-spacing: 1.6px; color: var(--ink-body);
  }
  .vote-banner {
    position: absolute; top: 466px; left: 0; right: 0;
    font-family: "Oswald", sans-serif; font-weight: 700; font-size: 58px;
    line-height: 70px; color: var(--ink-dark); letter-spacing: 0.5px;
  }
</style>
</head>
<body>

<section class="flyer flyer--front">
  <div class="corner-deco corner-deco--left" role="img" aria-label="Faint flag stars and stripes decoration"></div>
  <div class="corner-deco corner-deco--right" role="img" aria-label="Faint flag stars and stripes decoration"></div>

  <div class="brand-mark">
    <span class="brand-mark__dot"></span>
    <span>Neighbors Together</span>
  </div>

  <h1 class="front-title">THE NEIGHBORS<br>TOGETHER PROJECT</h1>

  <svg class="flag-art" viewBox="0 0 435 170" role="img" aria-label="Waving national flag illustration">
    <defs>
      <linearGradient id="flagTone" x1="0" x2="1" y1="0" y2="0">
        <stop offset="0" stop-color="#2a2a2a"/>
        <stop offset="0.35" stop-color="#9a9a9a"/>
        <stop offset="1" stop-color="#d8d8d8"/>
      </linearGradient>
    </defs>
    <path d="M0 45 C120 10 200 40 270 45 C340 50 380 0 435 0 L435 40 C380 40 350 100 270 110 C190 120 120 100 0 165 Z" fill="url(#flagTone)"/>
  </svg>

  <p class="slogan-lead">NEIGHBORS TOGETHER</p>
  <p class="slogan-big">One Road...<br>One Heart,</p>
  <p class="slogan-tail">Just a Different Stride</p>
  <span class="copyright-tag">JT PELLOW COPYRIGHTS©</span>
</section>

<section class="flyer flyer--back">
  <div class="corner-deco corner-deco--left" role="img" aria-label="Faint flag stars and stripes decoration"></div>
  <div class="corner-deco corner-deco--right" role="img" aria-label="Faint flag stars and stripes decoration"></div>

  <h2 class="poem-title">FIELD OF<br>QUIET LANTERNS</h2>
  <p class="poem-author">BY JT PELLOW</p>

  <div class="poem-body">
    <p>When evening settles on the field and porch lights start to glow,<br>each window holds a lantern lit for neighbors that we know.</p>
    <p>Some lanterns came from distant shores, some burned here long ago,<br>yet side by side they light the path wherever we may go.</p>
    <p>We carry flames from many homes, from valley, coast and plain, and every light we share tonight will help us through the rain.</p>
    <p>A quiet lantern, steady hand, a door left open wide... together we can walk the road, each with a different stride.</p>
    <p>So keep your lantern burning bright and pass the flame along.<br>For one small light may flicker, but a field of them is strong.</p>
  </div>

  <div class="poem-rule"></div>
  <p class="site-url">www.neighborstogetherhub.org</p>
  <p class="vote-banner">VOTE BLUE 2024</p>
</section>

</body>
</html>
```